Bar and Grill needs specials signage

I have attached a file called "daily specials" I need it changed - so there is 1 sign/poster for each day/special
also attached other items to show some styling. I want the new posters chalkboard format, styled along the lines of the drink designs attached.
The designs should be scaleable, and editable, I will print locally

```html
<!DOCTYPE html>
<html lang="en">
<head>
<meta charset="utf-8">
<title>Daily Specials – Tuesday</title>
<link rel="stylesheet" href="https://fonts.googleapis.com/css2?family=Cabin+Sketch:wght@400;700&family=Yellowtail&display=swap">
<style>
  :root {
    --board: #2a2f2a;
    --board-haze: #545954;
    --chalk: #f7f7f2;
    --chalk-red: #ea4a2f;
    --chalk-lime: #c9d23e;
    --chalk-olive: #9ea63a;
    --art-tone: #6b706b;
  }
  html, body {
    margin: 0;
    padding: 0;
    width: 927px;
    height: 1200px;
    overflow: hidden;
    background: var(--board);
  }
  .poster {
    position: relative;
    width: 927px;
    height: 1200px;
    background:
      radial-gradient(ellipse 380px 300px at 470px 640px, var(--board-haze) 0%, rgba(84,89,84,0) 100%),
      radial-gradient(ellipse 300px 180px at 560px 330px, rgba(84,89,84,.55) 0%, rgba(84,89,84,0) 100%),
      var(--board);
    overflow: hidden;
  }
  .poster__lines {
    position: absolute;
    inset: 0;
  }
  .corner-ornament {
    position: absolute;
    width: 46px;
    height: 46px;
    border-radius: 50%;
    background: rgba(247,247,242,.18);
  }
  .corner-ornament--tl { left: 28px; top: 20px; }
  .corner-ornament--tr { right: 28px; top: 20px; }
  .corner-ornament--bl { left: 28px; bottom: 20px; }
  .corner-ornament--br { right: 28px; bottom: 20px; }

  .headline {
    position: absolute;
    left: 0;
    width: 927px;
    margin: 0;
    text-align: center;
  }
  .headline--kicker {
    top: 78px;
    left: 14px;
    font-family: "Cabin Sketch", cursive;
    font-weight: 700;
    font-size: 72px;
    letter-spacing: 2px;
    color: transparent;
    -webkit-text-stroke: 2.5px var(--chalk);
  }
  .headline--day {
    top: 158px;
    left: 20px;
    font-family: "Yellowtail", cursive;
    font-weight: 400;
    font-size: 190px;
    line-height: 1;
    color: var(--chalk);
  }
  .headline--offer {
    top: 452px;
    left: 8px;
    font-family: "Cabin Sketch", cursive;
    font-weight: 700;
    font-size: 66px;
    letter-spacing: 3px;
    color: var(--chalk-red);
  }
  .headline--time {
    top: 968px;
    left: 8px;
    font-family: "Cabin Sketch", cursive;
    font-weight: 700;
    font-size: 62px;
    letter-spacing: 3px;
    color: var(--chalk);
  }
  .dish-art {
    position: absolute;
    left: 196px;
    top: 612px;
    width: 564px;
    height: 310px;
    border-radius: 48% 52% 46% 54% / 55% 50% 50% 45%;
    background: radial-gradient(ellipse at 50% 45%, var(--art-tone) 0%, rgba(107,112,107,.35) 60%, rgba(107,112,107,0) 100%);
  }
</style>
</head>
<body>
<main class="poster">
  <svg class="poster__lines" width="927" height="1200" viewBox="0 0 927 1200" aria-hidden="true">
    <g fill="none" stroke="var(--chalk)" stroke-linecap="round">
      <rect class="frame" x="42" y="32" width="846" height="1136" stroke-width="4"/>
      <line x1="176" y1="390" x2="772" y2="390" stroke-width="4"/>
      <line x1="152" y1="416" x2="612" y2="416" stroke-width="4"/>
      <line x1="152" y1="560" x2="772" y2="560" stroke-width="4"/>
      <line x1="152" y1="1064" x2="774" y2="1064" stroke-width="4"/>
      <line x1="246" y1="1082" x2="708" y2="1082" stroke-width="4"/>
    </g>
    <g class="accent-dashes" stroke="var(--chalk-lime)" stroke-width="2.5" stroke-linecap="round">
      <line x1="112" y1="190" x2="136" y2="197"/>
      <line x1="84" y1="267" x2="128" y2="267"/>
      <line x1="100" y1="342" x2="134" y2="338"/>
      <line x1="792" y1="192" x2="824" y2="182"/>
      <line x1="808" y1="258" x2="848" y2="257"/>
      <line x1="800" y1="328" x2="836" y2="332"/>
    </g>
    <g class="pointer-arrows" fill="none" stroke="var(--chalk-olive)" stroke-width="3" stroke-linejoin="round">
      <path d="M818 548 L834 562 L790 612 L800 622 L768 640 L774 604 L784 614 Z"/>
      <path d="M124 830 L144 822 L172 872 L184 866 L188 904 L156 888 L166 882 Z"/>
    </g>
  </svg>

  <div class="corner-ornament corner-ornament--tl" role="img" aria-label="Chalk flourish ornament"></div>
  <div class="corner-ornament corner-ornament--tr" role="img" aria-label="Chalk flourish ornament"></div>
  <div class="corner-ornament corner-ornament--bl" role="img" aria-label="Chalk flourish ornament"></div>
  <div class="corner-ornament corner-ornament--br" role="img" aria-label="Chalk flourish ornament"></div>

  <h2 class="headline headline--kicker">DAILY SPECIALS</h2>
  <h1 class="headline headline--day">Tuesday</h1>
  <p class="headline headline--offer">55 CENT WINGS</p>
  <div class="dish-art" role="img" aria-label="Chalk sketch of three chicken wings with a dipping sauce cup and a herb leaf"></div>
  <p class="headline headline--time">AFTER 3:00 PM</p>
</main>
</body>
</html>
```